Velmarotix - world unique technology for better life - please let them know who am i at first sight

We need a new business card for company which is a provider of unique crystal based technology suitable for all living being. For more information and final design you can use our brochure (our colours are black and blue from brochure).
We use Verdana font

Industry/Entity Type

Business

Contact Information for Business Card

regular dimension

Font styles to use
Other font styles liked:
• Verdana

Requirements
Must have
• Logo
• name
• function/position
• phone
• mobile
• e-mail
• adress
Nice to have
• inovative design (technology directed)

```html
<!DOCTYPE html>
<html lang="en">
<head>
<meta charset="UTF-8">
<title>Velmarotix Technologies – Business Card</title>
<link rel="stylesheet" href="https://fonts.googleapis.com/css2?family=Lato:wght@300;400&display=swap">
<style>
  :root {
    --page-bg: #e9ecef;
    --ink: #141619;
    --ink-soft: #3a3f46;
    --brand-blue: #1fb9dc;
    --brand-blue-deep: #0f9fc7;
    --frost-1: #f2f6fa;
    --frost-2: #c9d6e4;
    --frost-3: #9fb1c6;
    --white: #ffffff;
  }
  * { box-sizing: border-box; margin: 0; padding: 0; }
  html, body {
    width: 1200px; height: 858px; overflow: hidden;
    background: var(--page-bg);
    font-family: "Lato", Verdana, sans-serif;
    color: var(--ink);
  }
  .sheet {
    position: relative; width: 1200px; height: 858px;
    display: flex; align-items: center; justify-content: center; gap: 40px;
  }
  .card {
    position: relative; width: 540px; height: 309px; overflow: hidden;
    border-radius: 3px; box-shadow: 0 6px 18px rgba(20,30,45,.18);
  }
  .card__photo {
    position: absolute; inset: 0;
    background:
      radial-gradient(ellipse at 55% 60%, rgba(255,255,255,.55), transparent 55%),
      linear-gradient(160deg, var(--frost-1) 0%, var(--frost-2) 45%, var(--frost-3) 80%, var(--frost-2) 100%);
  }
  /* front */
  .brand {
    position: absolute; left: 150px; top: 118px;
    display: flex; align-items: center; gap: 14px;
  }
  .brand__dot { width: 46px; height: 46px; border-radius: 50%; background: var(--ink); }
  .brand__name { font-size: 36px; font-weight: 300; letter-spacing: 1px; line-height: 1; }
  .brand__sub { font-size: 10px; letter-spacing: 9px; margin-top: 6px; color: var(--ink-soft); }
  .brand__reg { font-size: 11px; vertical-align: top; }

  /* back */
  .back__band { position: absolute; inset: 0; }
  .back__logo {
    position: absolute; left: 34px; top: 120px; color: var(--white);
  }
  .back__logo .brand__name { font-size: 24px; }
  .back__logo .brand__sub { font-size: 7px; letter-spacing: 6px; color: var(--white); margin-top: 5px; }
  .person {
    position: absolute; right: 30px; top: 38px; text-align: right;
  }
  .person__name { font-size: 22px; font-weight: 300; }
  .person__role { font-size: 11px; margin-top: 4px; color: var(--ink-soft); }
  .contacts {
    position: absolute; right: 30px; bottom: 28px; list-style: none; text-align: right;
    font-size: 11.5px; line-height: 1.55;
  }
  .contacts li { display: flex; justify-content: flex-end; align-items: flex-start; gap: 8px; }
  .contacts svg { width: 11px; height: 11px; margin-top: 3px; flex: none; }
</style>
</head>
<body>
<main class="sheet">

  <section class="card card--front" aria-label="Card front">
    <div class="card__photo" role="img" aria-label="Soft blue laboratory background with crystal molecules and chemical structure diagrams"></div>
    <div class="brand">
      <span class="brand__dot"></span>
      <div>
        <div class="brand__name">VELMAROTIX<span class="brand__reg">®</span></div>
        <div class="brand__sub">TECHNOLOGIES</div>
      </div>
    </div>
  </section>

  <section class="card card--back" aria-label="Card back">
    <div class="card__photo" role="img" aria-label="Soft blue laboratory background with crystal molecules"></div>
    <svg class="back__band" viewBox="0 0 540 309" preserveAspectRatio="none" aria-hidden="true">
      <defs>
        <linearGradient id="bandBlue" x1="0" y1="0" x2="1" y2="1">
          <stop offset="0" stop-color="var(--brand-blue-deep)"/>
          <stop offset="1" stop-color="var(--brand-blue)"/>
        </linearGradient>
      </defs>
      <path d="M0 0 H215 Q300 160 205 309 H0 Z" fill="url(#bandBlue)"/>
      <path d="M215 0 Q300 160 205 309" fill="none" stroke="var(--white)" stroke-width="7"/>
    </svg>
    <div class="back__logo">
      <div class="brand__name">VELMAROTIX<span class="brand__reg">®</span></div>
      <div class="brand__sub">TECHNOLOGIES</div>
    </div>
    <div class="person">
      <div class="person__name">Your Name</div>
      <div class="person__role">Position</div>
    </div>
    <ul class="contacts">
      <li>000-0000-0000
        <svg viewBox="0 0 12 12"><rect x="3" y="0.5" width="6" height="11" rx="1" fill="none" stroke="currentColor"/><circle cx="6" cy="9.5" r=".7"/></svg></li>
      <li>+385(0) 51 402 937
        <svg viewBox="0 0 12 12"><path d="M2 1 L4.5 1 L5.5 3.5 L4 4.8 Q5.2 7 7.2 8 L8.5 6.5 L11 7.5 L11 10 Q6 11 3 8 Q1 5 2 1Z"/></svg></li>
      <li>info@velmarotix.eu
        <svg viewBox="0 0 12 12"><rect x="0.5" y="2" width="11" height="8" fill="none" stroke="currentColor"/><path d="M0.5 2 L6 7 L11.5 2" fill="none" stroke="currentColor"/></svg></li>
      <li>www.velmarotix.eu
        <svg viewBox="0 0 12 12"><circle cx="6" cy="6" r="5.3" fill="none" stroke="currentColor"/><ellipse cx="6" cy="6" rx="2.3" ry="5.3" fill="none" stroke="currentColor"/><path d="M0.7 6 H11.3" stroke="currentColor"/></svg></li>
      <li>28-34 Harrow Lane London<br>N7 2QD &nbsp;United Kingdom
        <svg viewBox="0 0 12 12"><path d="M6 11.5 Q1.5 6.5 1.5 4.5 A4.5 4.5 0 0 1 10.5 4.5 Q10.5 6.5 6 11.5Z"/><circle cx="6" cy="4.5" r="1.6" fill="var(--white)"/></svg></li>
    </ul>
  </section>

</main>
</body>
</html>
```